Meridale Bed Company Needs Business Card

Looking for a very nice looking business card. Creative but not extravagant. We sell beds and pillows across the U.S. and need something professional but catchy. I have attached the logo.

Name : Devin Holt
Title : President
Phone : (800) 471-2960
Email: sleep@quilmora.com
Website: www.quilmora.com

Can be single-sided or double-sided
horizontal or vertical

Can use Blues/Greys

Target Market(s)

Mass Market

Industry/Entity Type

Retail

Contact Information for Business Card

Name : Devin Holt
Title : President
Phone : (800) 471-2960
Email: sleep@quilmora.com
Website: www.quilmora.com

Requirements
Must have
• Clean, Modern, Smooth
• Can use Blues/Greys
• On the other side without the information - have something simple like www.quilmora.com or our logo
Nice to have
• Surprise me
Should not have
• Nothing crazy, nothing cluttered

```html
<!DOCTYPE html>
<html lang="en">
<head>
<meta charset="UTF-8">
<title>Quilmora Business Card</title>
<link rel="stylesheet" href="https://fonts.googleapis.com/css2?family=Figtree:wght@300;400&display=swap">
<style>
  :root {
    --backdrop: #dfe2e3;
    --brand-blue: #4dd0f4;
    --accent-blue: #3ec9f0;
    --card-white: #ffffff;
    --ink: #3a3a3a;
    --shadow: rgba(0, 0, 0, 0.22);
  }
  * { margin: 0; padding: 0; box-sizing: border-box; }
  html, body {
    width: 1200px;
    height: 761px;
    overflow: hidden;
    background: var(--backdrop);
    font-family: "Figtree", sans-serif;
  }
  .stage {
    position: relative;
    width: 1200px;
    height: 761px;
  }
  .card {
    position: absolute;
    top: 271px;
    height: 229px;
    box-shadow: 6px 6px 10px var(--shadow);
  }
  .card--front {
    left: 156px;
    width: 398px;
    background: var(--brand-blue);
    display: flex;
    align-items: center;
    justify-content: center;
  }
  .card--back {
    left: 618px;
    width: 402px;
    background: var(--card-white);
  }
  .wordmark {
    font-weight: 300;
    letter-spacing: 0.5px;
    line-height: 1;
  }
  .card--front .wordmark {
    color: var(--card-white);
    font-size: 50px;
    margin-top: 2px;
  }
  .card--back .wordmark {
    position: absolute;
    left: 32px;
    top: 24px;
    color: var(--accent-blue);
    font-size: 48px;
  }
  .holder {
    position: absolute;
    left: 35px;
    top: 101px;
  }
  .holder__name {
    color: var(--accent-blue);
    font-size: 15px;
    font-weight: 400;
    line-height: 18px;
  }
  .holder__title {
    color: var(--ink);
    font-size: 11px;
    line-height: 16px;
    margin-top: 2px;
  }
  .contact, .address {
    position: absolute;
    top: 161px;
    color: var(--ink);
    font-size: 11.5px;
    line-height: 16px;
    list-style: none;
  }
  .contact { left: 35px; }
  .address {
    right: 30px;
    top: 177px;
    font-style: normal;
  }
</style>
</head>
<body>
  <main class="stage">
    <section class="card card--front" aria-label="Card front">
      <span class="wordmark">quilmora</span>
    </section>

    <section class="card card--back" aria-label="Card back">
      <span class="wordmark">quilmora</span>
      <div class="holder">
        <p class="holder__name">Devin Holt</p>
        <p class="holder__title">President</p>
      </div>
      <ul class="contact">
        <li>T (800) 471-2960</li>
        <li>E sleep@quilmora.com</li>
        <li>W www.quilmora.com</li>
      </ul>
      <address class="address">
        14 Larkin Street,<br>
        Bellmont NSW 2071
      </address>
    </section>
  </main>
</body>
</html>
```